Cleaning Service Company In need of Good Web presence.

The company is a cleaning service company which provides professional staff and service for cleaning. This is a project to build a site that is both solid and a strong recognition of our organization. It is supposed to show quality, cleanliness, professionalism. The use of images and art for imagery is all good just to have a site that is consistent and solid. There might be a chance to make stationary, logo and business cars if someone feels they can build a brand that is consistent. The image we are going for is clean solid and to stand out. Finally stationary should not be expensive to print.

Current logo is attached and can be used or can be made more creative.

Target Market(s)

Corporate and Government entities, that will feel that this company has a brand that sets it apart from the rest. The company is new so the modification of the logo will not be an issue if a more solid brand come out of this project. The idea is to have a clean consistent product that stands our from others in terms of website, stationary, etc

Industry/Entity Type

Cleaning Service

Contact Information for Business Card

P.O.Box 51947
Riffa
Kingdom of Bahrain

Logo Text

Harbor Lane Services

Number of Pages Required

4 page

Font styles to use
Sans Serif

Colors
abd036
cadf82
eaf2ce
9bcb3b

Requirements
Must have
• Green Color to be used in order to stick to the name. Also the creativity and boldness in an elegant manner.
Nice to have
• Arabic name of company
• هاربر لين سرفسس ذ.م.م
• if cannot be put at least make a location should be chosen
• Also could be a bit of 3D given to the logo if it could stay elegent.
Should not have
• Should not show people cleaning.

```html
<!DOCTYPE html>
<html lang="en">
<head>
<meta charset="utf-8">
<title>Harbor Lane Services</title>
<link rel="stylesheet" href="https://fonts.googleapis.com/css2?family=Roboto:wght@400;500;700;900&family=Open+Sans:wght@400;600;700&display=swap">
<style>
:root{
  --green:#8cc63f;
  --green-dark:#3f9a3a;
  --green-deep:#1f8a4c;
  --green-band:#23935a;
  --lime:#abd036;
  --lime-soft:#cadf82;
  --lime-pale:#eaf2ce;
  --ink:#333;
  --muted:#777;
  --dark:#232323;
  --darker:#1a1a1a;
  --white:#fff;
  --grey:#f1f1f1;
}
*{box-sizing:border-box;margin:0;padding:0}
html,body{width:1200px;height:2888px;overflow:hidden}
body{font-family:"Open Sans",sans-serif;color:var(--ink);background:var(--white);position:relative;font-size:12px;line-height:1.6}
h1,h2,h3,h4{font-family:"Roboto",sans-serif}
.section{position:absolute;left:0;width:1200px}

/* header */
.site-header{top:0;height:120px;background:var(--white)}
.brand{position:absolute;left:118px;top:4px;width:124px;height:124px;border-radius:50%;background:var(--white);border:5px solid var(--green);display:flex;align-items:center;justify-content:center;text-align:center;z-index:3;padding:12px}
.brand span{font-family:"Roboto",sans-serif;font-weight:700;color:var(--green-dark);font-size:15px;line-height:1.2}
.main-nav{position:absolute;left:100px;right:100px;top:74px;height:34px;background:var(--green);display:flex;align-items:center;padding-left:170px;gap:30px;z-index:2}
.main-nav a{color:var(--white);font-family:"Roboto",sans-serif;font-weight:500;font-size:12px;text-decoration:none;letter-spacing:.5px}
.main-nav .search{margin-left:auto;margin-right:14px}
.quote-call{position:absolute;right:110px;top:12px;text-align:right}
.quote-call small{display:block;color:var(--green-dark);font-size:13px;font-weight:600}
.quote-call strong{font-family:"Roboto",sans-serif;font-size:30px;color:var(--green-dark);font-weight:700;line-height:1.1}
.quote-call svg{vertical-align:middle;margin-right:6px}

/* hero */
.hero{top:108px;height:494px;background:linear-gradient(180deg,#9cc9ea 0%,#cfe3ef 38%,#8aa6b4 52%,#5f8f3e 62%,#7fbf3a 80%,#9bcb3b 100%)}
.hero-bar{top:602px;height:34px;background:var(--green);display:flex;align-items:center;justify-content:center;gap:10px}
.hero-bar i{width:11px;height:11px;border-radius:50%;background:var(--white);opacity:.6}
.hero-bar i.on{opacity:1}

/* services */
.services{top:660px;height:320px;display:flex;justify-content:center;gap:60px}
.service{width:300px;text-align:center}
.service .icon{width:92px;height:92px;border-radius:50%;background:var(--green-dark);margin:0 auto 16px;display:flex;align-items:center;justify-content:center}
.service h3{color:var(--green-dark);font-size:22px;font-weight:500}
.service .sub{color:var(--muted);font-size:12px;margin-bottom:10px}
.service p{text-align:left;color:var(--muted);font-size:12px}
.btn-dark{display:inline-block;margin-top:18px;background:var(--dark);color:var(--white);font-size:11px;padding:7px 16px;border-radius:3px}
.btn-dark::before{content:"";display:inline-block;width:6px;height:6px;border-radius:50%;background:var(--green);margin-right:6px;vertical-align:middle}

/* welcome */
.welcome{top:1010px;height:360px}
.welcome-art{position:absolute;left:160px;top:10px;width:280px;height:300px;background:linear-gradient(180deg,#f3f8e6,#c6e08a 70%,#8cc63f)}
.welcome-copy{position:absolute;left:480px;top:0;width:560px}
.welcome-copy h2{font-size:25px;font-weight:700;color:var(--ink)}
.welcome-copy h2 b{color:var(--green-dark)}
.welcome-copy p{color:var(--muted);margin:10px 0}
.btn-outline{display:inline-block;border:2px solid var(--ink);padding:6px 18px;font-weight:700;font-size:11px;margin:6px 0 24px}
.features{display:flex;gap:26px}
.feature{width:170px}
.feature .fi{width:46px;height:46px;border-radius:50%;background:var(--green-dark);display:flex;align-items:center;justify-content:center;margin-bottom:8px}
.feature h4{font-size:11px;font-weight:700}
.feature p{font-size:11px;margin:4px 0 0}

/* band */
.band{top:1390px;height:440px;background:linear-gradient(120deg,var(--green-band),#2fa364 55%,var(--green-deep))}
.band-copy{position:absolute;left:160px;top:44px;width:560px;color:var(--white)}
.band-copy h2{font-size:33px;font-weight:400;line-height:1.2}
.band-copy p{font-size:12px;opacity:.9;margin-top:12px}
.band-cols{display:flex;gap:30px;margin-top:22px}
.band-cols div{width:265px}
.band-cols h3{font-size:24px;font-weight:400}
.btn-light{display:inline-block;margin-top:20px;border:1px solid var(--white);color:var(--white);padding:6px 16px;font-size:11px}
.band-photo{position:absolute;right:150px;top:30px;width:320px;height:410px;background:linear-gradient(180deg,rgba(255,255,255,.15),rgba(240,200,80,.55) 70%,rgba(255,150,40,.6))}

/* testimonials */
.experts{top:1860px;height:480px;text-align:center}
.experts h2{font-size:32px;font-weight:900;letter-spacing:1px}
.experts h2 b{color:var(--green-dark)}
.experts .lead{color:var(--muted);width:800px;margin:8px auto 30px}
.quotes{display:flex;justify-content:center;gap:70px}
.quote{width:280px}
.quote .ph{width:150px;height:150px;border-radius:50%;margin:0 auto;border:4px solid var(--lime-soft);background:linear-gradient(160deg,var(--lime-pale),#b9cfd6)}
.quote h4{font-size:12px;font-weight:500;margin:14px 0 8px;color:var(--muted)}
.quote h4::before,.quote h4::after{content:"";display:inline-block;width:50px;height:1px;background:#ccc;vertical-align:middle;margin:0 10px}
.quote p{color:var(--muted);font-size:12px;text-align:left}
.dots{display:flex;justify-content:center;gap:6px;margin-top:24px}
.dots i{width:40px;height:4px;background:#ccc}
.dots i.on{background:var(--dark)}

/* partners */
.partners{top:2360px;height:140px;background:var(--grey);display:flex;align-items:center;justify-content:center;gap:26px}
.arrow{width:40px;height:40px;background:var(--green-deep);display:flex;align-items:center;justify-content:center;transform:rotate(45deg)}
.arrow svg{transform:rotate(-45deg)}
.partner{width:160px;height:90px;background:var(--white);display:flex;align-items:center;justify-content:center}

/* footer */
.site-footer{top:2500px;height:340px;background:var(--dark);color:#aaa}
.fcol{position:absolute;top:34px;width:290px}
.fcol h4{color:var(--white);font-size:15px;font-weight:500;padding-bottom:8px;border-bottom:1px solid #444;margin-bottom:14px}
.fcol p{font-size:11px}
.social{display:flex;gap:8px;margin-top:16px}
.social i{width:26px;height:26px;border-radius:50%;background:#444}
.field{height:26px;background:#2e2e2e;border:1px solid #3a3a3a;margin-bottom:10px;font-size:11px;padding:4px 8px;color:#888}
.field.tall{height:56px}
.btn-green{display:inline-block;background:var(--lime);color:var(--dark);font-weight:700;font-size:11px;padding:5px 18px;border-radius:3px}
.tweet{display:flex;gap:10px;margin-bottom:14px;font-size:11px}
.tweet svg{flex:none;margin-top:3px}
.contact-strip{position:absolute;left:160px;right:160px;top:296px;display:flex;justify-content:space-between;align-items:center;font-size:11px}
.contact-strip .pill{background:var(--lime);color:var(--dark);padding:4px 14px;font-weight:700;border-radius:3px}
.bottom-bar{top:2840px;height:48px;background:var(--darker);color:#888;font-size:11px;display:flex;align-items:center;justify-content:space-between;padding:0 160px}
.bottom-bar nav{display:flex;gap:16px}
</style>
</head>
<body>

<header class="section site-header">
  <div class="brand"><span>Harbor Lane Services</span></div>
  <nav class="main-nav">
    <a>HOME</a><a>ABOUT US</a><a>SERVICES</a><a>GALLERY</a><a>QUOTES</a><a>TESTIMONIALS</a><a>PAYMENTS</a><a>CONTACT US</a>
    <a class="search"><svg width="14" height="14" viewBox="0 0 14 14"><circle cx="6" cy="6" r="4.5" fill="none" stroke="#fff" stroke-width="2"/><path d="M9.5 9.5 13 13" stroke="#fff" stroke-width="2"/></svg></a>
  </nav>
  <div class="quote-call">
    <small>Call Us for a Quote</small>
    <strong><svg width="24" height="24" viewBox="0 0 24 24"><path d="M6 2l4 4-2 3c1.5 3 4 5.5 7 7l3-2 4 4-3 4C10 21 3 14 2 5z" fill="#3f9a3a"/></svg>302-555-0147</strong>
  </div>
</header>

<div class="section hero" role="img" aria-label="City skyline above a red farmhouse and a wide green lawn"></div>
<div class="section hero-bar"><i></i><i class="on"></i><i></i></div>

<section class="section services">
  <div class="service">
    <div class="icon"><svg width="46" height="46" viewBox="0 0 46 46"><path d="M8 22 23 9l15 13v16H8z" fill="none" stroke="#fff" stroke-width="3"/><path d="M19 38V28h8v10" fill="none" stroke="#fff" stroke-width="3"/></svg></div>
    <h3>Residential Cleaning</h3>
    <div class="sub">Subtext Ipsum</div>
    <p>Our home team keeps every room spotless with careful, eco friendly products, flexible weekly visits and fully vetted staff you can trust inside your home, every single time.</p>
    <span class="btn-dark">Read More</span>
  </div>
  <div class="service">
    <div class="icon"><svg width="46" height="46" viewBox="0 0 46 46"><rect x="12" y="8" width="22" height="30" fill="none" stroke="#fff" stroke-width="3"/><path d="M17 15h4M25 15h4M17 22h4M25 22h4M17 29h4M25 29h4" stroke="#fff" stroke-width="3"/></svg></div>
    <h3>Commercial cleaning</h3>
    <div class="sub">Subtext Ipsum</div>
    <p>Offices, showrooms and government buildings cleaned after hours by trained crews, with clear checklists, reliable reporting and standards that stay high across every single site.</p>
    <span class="btn-dark">Read More</span>
  </div>
  <div class="service">
    <div class="icon"><svg width="46" height="46" viewBox="0 0 46 46"><path d="M10 36C10 18 22 10 38 10c0 18-10 26-28 26z" fill="none" stroke="#fff" stroke-width="3"/><path d="M12 34 30 18" stroke="#fff" stroke-width="3"/></svg></div>
    <h3>Green Cleaning</h3>
    <div class="sub">Subtext Ipsum</div>
    <p>Plant based solutions and low water methods that protect people and the planet, leaving fresh, healthy spaces without harsh chemicals, strong odours or any lasting residue.</p>
    <span class="btn-dark">Read More</span>
  </div>
</section>

<section class="section welcome">
  <div class="welcome-art" role="img" aria-label="Green line illustration of a clean city with buildings and trees"></div>
  <div class="welcome-copy">
    <h2>WELCOME TO <b>HARBOR LANE SERVICES</b></h2>
    <p>Harbor Lane Services is a new cleaning company serving corporate and government clients across the Kingdom of Bahrain. We bring trained people, modern equipment and a calm, professional approach to every building we care for, large or small.</p>
    <p>From daily office upkeep to deep cleans and special projects, our teams follow clear standards and report on every visit, so you always know the work is done properly and on time.</p>
    <span class="btn-outline">READ MORE</span>
    <div class="features">
      <div class="feature">
        <div class="fi"><svg width="24" height="24" viewBox="0 0 24 24"><circle cx="12" cy="8" r="4" fill="#fff"/><path d="M4 22c0-5 4-8 8-8s8 3 8 8z" fill="#fff"/></svg></div>
        <h4>HIGHLY TRAINED STAFF</h4>
        <p>Skilled, vetted teams trained to strict quality checklists.</p>
      </div>
      <div class="feature">
        <div class="fi"><svg width="24" height="24" viewBox="0 0 24 24"><path d="M12 3c4 5 6 8 6 11a6 6 0 0 1-12 0c0-3 2-6 6-11z" fill="#fff"/></svg></div>
        <h4>ECO-SAFE CLEANING TOOLS</h4>
        <p>Gentle products that are safe for people and surfaces.</p>
      </div>
      <div class="feature">
        <div class="fi"><svg width="24" height="24" viewBox="0 0 24 24"><path d="M4 12l5 5L20 6" fill="none" stroke="#fff" stroke-width="3"/></svg></div>
        <h4>FAST &amp; EFFECTIVE SERVICE</h4>
        <p>Quick response times with results you can see.</p>
      </div>
    </div>
  </div>
</section>

<section class="section band">
  <div class="band-copy">
    <h2>The Best Cleaning Company In The Country</h2>
    <p>We combine careful people, proven methods and honest pricing to keep workplaces clean, safe and welcoming. Every contract comes with a dedicated supervisor and regular quality checks.</p>
    <div class="band-cols">
      <div>
        <h3>Company History</h3>
        <p>Founded in Riffa with a small team and a clear goal: raise the standard of building care for local businesses.</p>
      </div>
      <div>
        <h3>Our Philosophy</h3>
        <p>Clean spaces build trust. We work quietly, respect every site and always leave things better than we found them.</p>
      </div>
    </div>
    <span class="btn-light">Read More</span>
  </div>
  <div class="band-photo" role="img" aria-label="Cleaner holding a bucket of cleaning supplies"></div>
</section>

<section class="section experts">
  <h2>WHAT SAY'S OUR <b>EXPERTS</b></h2>
  <p class="lead">Clients across Bahrain rely on our teams every day. Here is what a few of them say about working with Harbor Lane Services.</p>
  <div class="quotes">
    <div class="quote">
      <div class="ph" role="img" aria-label="Portrait of a client"></div>
      <h4>Nadia Farouk</h4>
      <p>“Reliable, friendly and thorough. Our offices have never looked better, and the team always arrives exactly on time.”</p>
    </div>
    <div class="quote">
      <div class="ph" role="img" aria-label="Portrait of a client"></div>
      <h4>Karim Haddad</h4>
      <p>“Clear reports after every visit and a supervisor who answers quickly. It makes managing our buildings easy.”</p>
    </div>
    <div class="quote">
      <div class="ph" role="img" aria-label="Portrait of a client"></div>
      <h4>Lena Marsh</h4>
      <p>“Their green products were a big reason we chose them. The results are excellent and the staff are very polite.”</p>
    </div>
  </div>
  <div class="dots"><i class="on"></i><i></i><i></i></div>
</section>

<section class="section partners">
  <div class="arrow"><svg width="14" height="14" viewBox="0 0 14 14"><path d="M9 2 4 7l5 5" fill="none" stroke="#fff" stroke-width="2"/></svg></div>
  <div class="partner"><svg width="80" height="40"><rect x="20" y="4" width="40" height="32" rx="4" fill="#d9d9d9"/></svg></div>
  <div class="partner"><svg width="80" height="40"><circle cx="40" cy="20" r="17" fill="#d9d9d9"/></svg></div>
  <div class="partner"><svg width="80" height="40"><rect x="20" y="4" width="40" height="32" rx="4" fill="#d9d9d9"/></svg></div>
  <div class="partner"><svg width="80" height="40"><circle cx="40" cy="20" r="17" fill="#d9d9d9"/></svg></div>
  <div class="partner"><svg width="80" height="40"><rect x="20" y="4" width="40" height="32" rx="4" fill="#d9d9d9"/></svg></div>
  <div class="arrow"><svg width="14" height="14" viewBox="0 0 14 14"><path d="M5 2l5 5-5 5" fill="none" stroke="#fff" stroke-width="2"/></svg></div>
</section>

<footer class="section site-footer">
  <div class="fcol" style="left:160px">
    <h4>About Company</h4>
    <p>Harbor Lane Services provides professional cleaning for corporate and government clients.</p>
    <p>P.O.Box 51947, Riffa, Kingdom of Bahrain</p>
    <p dir="rtl" style="text-align:left">هاربر لين سرفسس ذ.م.م</p>
    <div class="social"><i></i><i></i><i></i><i></i></div>
  </div>
  <div class="fcol" style="left:455px">
    <h4>Request Quote</h4>
    <div class="field">Name</div>
    <div class="field">Email</div>
    <div class="field tall">Message</div>
    <span class="btn-green">Submit</span>
  </div>
  <div class="fcol" style="left:750px">
    <h4>Latest Tweets</h4>
    <div class="tweet"><svg width="12" height="12"><rect width="12" height="12" fill="#666"/></svg><p>New office contracts starting this month across Manama and Riffa. 2 days ago</p></div>
    <div class="tweet"><svg width="12" height="12"><rect width="12" height="12" fill="#666"/></svg><p>Our eco-safe cleaning range is now used on every site we service. 5 days ago</p></div>
    <div class="tweet"><svg width="12" height="12"><rect width="12" height="12" fill="#666"/></svg><p>Thank you to our clients for a great first quarter together. 1 week ago</p></div>
  </div>
  <div class="contact-strip">
    <span>hello@harborlaneservices.example</span>
    <span class="pill">Call Now : 302-555-0198</span>
  </div>
</footer>

<div class="section bottom-bar">
  <span>© Harbor Lane Services. All rights reserved.</span>
  <nav><span>Home</span><span>About Us</span><span>Services</span><span>Quotes</span><span>Contact Us</span></nav>
</div>

</body>
</html>
```